Corvanth Veylor - Advanced Skincare and undetectable Makeup for Men

We are in need of a professional webpage for our company Corvanth Veylor. We help every man feel his best by looking his best. Inspired by the myth of Corvanth, we offer makeup and skincare products along with education upon their use. Our mission is to celebrate masculinity in all of its forms, regardless of age, race, sexual orientation, or assigned gender at birth.

The webpage would serve as our online store, as a place where our clients can learn about our brand, view our "How-to" video tutorials, and get product information. An online blog will also be hosted in order to keep clients up to date with news, updates, media mentions, etc.

The color schemes that we use are mostly Black and Gold, with Red accents. please keep in mind that this is a men's cosmetics line, and therefore should read powerful, sexy, confident and bold - all with a high end look and feel.

Think along the lines of brands like Lem Brisko, QDV, Belluti, etc.

our logo is included in the files attached. images and copy will be added in at a later time; hence, general images that fit the feel and filler text is encouraged.

The products to be sold include:
a face cleanser in a pump dispenser bottle (1 size)
a mask in a round jar container (1 size)
a moisturizer in a pump container 1 size)
a concealer in a click pen with a brush applicator (3 shades)
a liquid liner pen (4 shades)
a contouring palette (2 shade options)
a setting spray (single option)

Target Market(s)

Millennial Men

Industry/Entity Type

Beauty

Number of Pages Required

5+ page

Font styles to use
Serif

Colors
ec1f27
000000
faa54b

Requirements
Must have
• ur essential requirements are:
• 1) a stunning and engaging landing page that truly captures the ideals of sexuality, boldness and confidence.
• 2) an interactive and engaging online store that is easy to update / add product / information to.
• 3) Product pages supporting various toggling images of the product, a shade selection option, ingredient information, usage instructions, pricing, and a link to a "how to video" unique to each individual product.
• 4) dedicated space where all of the tutorials can be organized together
• 5) an organized Blog section, that would include a segment for a Q&A section for us to update as the brand grows, ongoing contests (that would be easily hidden if there are no contests running at the moment) as well as general news and updates segment.
• 6) an "about us" page, where our customers are able to learn about our story, inspirations, humanitarian efforts and philosophies in product contents and purity.
• 7) a contact us page, which would include social media links, contact email and telephone number as well as physical address to be updated upon launch.
• 8) discrete privacy policy, terms of use, and return policy links available at the bottom of every page
Nice to have
• 1) A posting forum where clients could post their looks using our products, or maybe a live stream of our Pictoval account.
• 2) a member sign in page so that we can collect and store customer information for faster check out, keep track of purchases attached to their email address (future loyalty program plans) and maintain an email database for email notifications and the such.

```html
<!DOCTYPE html>
<html lang="en">
<head>
<meta charset="utf-8">
<title>Corvanth Veylor — Skincare &amp; Makeup for Men</title>
<link href="https://fonts.googleapis.com/css2?family=Montserrat:wght@400;500;600;700;800&family=Open+Sans:wght@400;600&display=swap" rel="stylesheet">
<style>
:root{
  --red:#ec1f27;
  --black:#000000;
  --gold:#faa54b;
  --ink:#222222;
  --muted:#8a8a8a;
  --line:#e6e6e6;
  --soft:#f4f4f4;
  --white:#ffffff;
  --footer:#f7f7f7;
}
*{box-sizing:border-box;margin:0;padding:0}
html,body{width:1200px;height:4476px;overflow:hidden}
body{font-family:"Open Sans",Arial,sans-serif;color:var(--ink);background:var(--white);font-size:13px;line-height:1.6}
h1,h2,h3,h4{font-family:"Montserrat",Arial,sans-serif}
.btn{display:inline-block;font-family:"Montserrat",Arial,sans-serif;font-weight:600;font-size:13px;color:var(--white);background:var(--red);border-radius:26px;padding:12px 30px}

/* top bar */
.topbar{height:40px;background:var(--black);color:#cfcfcf;font-size:11px;display:flex;align-items:center;justify-content:space-between;padding:0 80px}
.topbar .contact span{margin-right:22px}
.topbar .social{display:flex;gap:12px;align-items:center}
.topbar .social i{width:9px;height:9px;border-radius:50%;background:#cfcfcf;display:block}
.topbar .prefs span{margin-left:24px}

/* nav */
.nav{height:112px;display:flex;align-items:center;padding:0 80px;border-bottom:1px solid var(--line)}
.brand{display:flex;align-items:center;gap:10px;font-family:"Montserrat",Arial,sans-serif;font-weight:700;font-size:17px;letter-spacing:2px;color:var(--black);text-transform:uppercase;width:360px}
.brand .mark{width:14px;height:14px;background:var(--black)}
.menu{display:flex;gap:28px;font-family:"Montserrat",Arial,sans-serif;font-size:11px;font-weight:600;letter-spacing:1px;flex:1}
.menu a{color:var(--ink);text-decoration:none}
.tools{display:flex;gap:16px}

/* hero */
.hero{height:588px;position:relative;background:linear-gradient(90deg,#c9c5b4 0%,#bcc0ab 50%,#b2b7a0 100%)}
.hero .photo{position:absolute;left:0;top:0;width:620px;height:588px;background:
  radial-gradient(ellipse 130px 170px at 300px 250px,#e3b9a2 0%,#cf9f87 60%,transparent 100%),
  radial-gradient(ellipse 260px 300px at 260px 200px,#5a3a2c 0%,#7b5644 55%,transparent 100%),
  radial-gradient(ellipse 300px 160px at 320px 560px,#1a1a1a 0%,#2b2b2b 60%,transparent 100%),
  linear-gradient(90deg,#bcbca8,#b8bba5)}
.hero .copy{position:absolute;right:60px;top:190px;width:420px;text-align:right}
.hero h1{font-size:40px;line-height:48px;font-weight:700;color:#1c1c1c}
.hero p{margin:14px 0 24px;color:#333;font-size:15px;line-height:1.5}

/* features */
.features{height:240px;display:flex;justify-content:space-around;padding:40px 100px 0}
.feature{width:280px;text-align:center}
.feature svg{display:block;margin:0 auto 10px}
.feature h3{color:var(--red);font-size:13px;font-weight:600;margin-bottom:8px}
.feature p{font-size:11px;color:var(--muted);line-height:1.5}

/* welcome */
.welcome{margin-top:12px;height:520px;position:relative;background:linear-gradient(90deg,#ececea 0%,#e2e1dc 55%,#d9dcd4 100%)}
.welcome .photo{position:absolute;right:0;top:0;width:640px;height:520px;background:
  radial-gradient(circle at 440px 260px,#ffffff 0%,#f2f0ee 22%,transparent 34%),
  radial-gradient(circle at 560px 120px,#e4b6d6 0%,transparent 18%),
  radial-gradient(circle at 560px 420px,#e0a9cc 0%,transparent 20%),
  linear-gradient(135deg,#e6e4df,#d2d6cc)}
.welcome .card{position:absolute;left:108px;top:128px;width:672px;height:268px;background:var(--white);padding:34px 44px;box-shadow:0 6px 24px rgba(0,0,0,.08)}
.eyebrow{font-family:"Montserrat",Arial,sans-serif;font-size:11px;letter-spacing:2px;color:var(--gold);font-weight:600}
.welcome h2{color:var(--gold);font-size:28px;font-weight:700;margin:6px 0 12px}
.welcome p{font-size:13px;color:#444;margin-bottom:22px;line-height:1.55}

/* trending */
.trending{padding-top:60px;height:1140px;text-align:center}
.section-title{font-family:"Montserrat",Arial,sans-serif;font-size:32px;font-weight:800;letter-spacing:1px}
.trending .section-title{color:var(--red)}
.lead{width:660px;margin:22px auto 0;font-size:12px;color:var(--muted);line-height:1.6}
.tabs{margin-top:26px;display:flex;justify-content:center;gap:18px}
.tabs span{font-family:"Montserrat",Arial,sans-serif;font-size:11px;font-weight:600;color:var(--white);background:var(--red);padding:7px 22px;border-radius:2px}
.tabs .active{background:var(--gold);color:var(--black)}
.grid{width:1024px;margin:38px auto 0;display:grid;grid-template-columns:repeat(5,188px);column-gap:21px;row-gap:32px}
.product{text-align:center}
.product .img{height:240px;background:var(--soft);position:relative}
.product .tag{position:absolute;top:8px;right:8px;background:var(--black);color:var(--white);font-size:9px;padding:1px 7px;font-weight:600}
.img.cleanser{background:radial-gradient(ellipse 60px 80px at 50% 55%,#8fb3cf 0%,#cfdde8 55%,#f4f4f4 100%)}
.img.mask{background:radial-gradient(ellipse 55px 40px at 50% 55%,#c9c9c9 0%,#e6e6e6 60%,#f4f4f4 100%)}
.img.moist{background:radial-gradient(ellipse 45px 90px at 50% 55%,#ffffff 0%,#f1dfd3 55%,#f4f4f4 100%)}
.img.conceal{background:linear-gradient(135deg,#8e8e8e 0%,#b9a48f 55%,#c9b39b 100%)}
.img.liner{background:linear-gradient(135deg,#f4f4f4 30%,#2a2a2a 48%,#2a2a2a 54%,#f4f4f4 70%)}
.img.palette{background:radial-gradient(ellipse 70px 60px at 50% 50%,#4a3a34 0%,#9a7a66 55%,#f4f4f4 100%)}
.img.spray{background:linear-gradient(90deg,#f4f4f4 10%,#9da3a8 25%,#2d2d2d 45%,#b9bec2 65%,#3a3a3a 80%,#f4f4f4 92%)}
.product .actions{position:absolute;left:0;right:0;bottom:0;display:flex}
.product .actions span{flex:1;font-size:9px;color:var(--white);background:var(--red);padding:5px 0;font-weight:600}
.product .actions span+span{background:var(--gold)}
.product h4{font-size:11px;font-weight:600;margin-top:12px;letter-spacing:.5px}
.product .price{font-size:11px;color:var(--muted)}
.product .price s{margin-left:6px}
.shades{display:flex;justify-content:center;gap:4px;margin-top:4px}
.shades i{width:10px;height:10px;display:block}
.all{margin-top:40px}

/* video */
.video{height:396px;display:flex;background:#f5f5f5}
.video .media{width:600px;height:396px;position:relative;background:
  radial-gradient(ellipse 120px 150px at 320px 170px,#e6c0a6 0%,#c99a80 60%,transparent 100%),
  radial-gradient(ellipse 230px 240px at 300px 180px,#6e4c3a 0%,transparent 100%),
  linear-gradient(90deg,#e9e3dc,#ddd3c9)}
.controls{position:absolute;left:82px;right:82px;bottom:20px;height:34px;background:rgba(0,0,0,.85);display:flex;align-items:center;padding:0 14px;gap:14px}
.controls .bar{flex:1;height:3px;background:#555;position:relative}
.controls .bar b{position:absolute;left:0;top:0;width:38%;height:3px;background:var(--gold)}
.controls em{font-style:normal;color:#ddd;font-size:10px}
.video .copy{padding:86px 0 0 40px;width:520px}
.video .section-title{color:var(--gold);font-size:30px}
.video p{font-size:12px;color:var(--muted);margin:16px 0 26px}

/* blog */
.blog{height:552px;padding-top:48px;text-align:center}
.blog .section-title{color:var(--gold);font-size:30px}
.posts{width:880px;margin:40px auto 0;display:flex;justify-content:space-between}
.post{width:272px;height:400px;background:var(--white);box-shadow:0 4px 18px rgba(0,0,0,.1);text-align:left;position:relative}
.post .head{display:flex;height:180px}
.post .date{width:60px;padding-top:12px;text-align:center;font-family:"Montserrat",Arial,sans-serif}
.post .date b{font-size:18px;display:block}
.post .date small{font-size:10px;letter-spacing:1px}
.post .date i{display:block;width:40px;height:22px;background:var(--red);margin:14px auto 0}
.post .pic{flex:1;margin:12px 12px 0 0}
.pic.one{background:radial-gradient(ellipse 50px 60px at 55% 50%,#e2b8a0 0%,transparent 100%),linear-gradient(135deg,#3c2c26,#b48e7a)}
.pic.two{background:radial-gradient(ellipse 50px 60px at 45% 55%,#e0bba6 0%,transparent 100%),linear-gradient(135deg,#d8d4d0,#5c5452)}
.pic.three{background:radial-gradient(ellipse 50px 60px at 40% 55%,#e8c3a8 0%,transparent 100%),linear-gradient(135deg,#f0ece8,#8a5a44)}
.post .body{padding:16px 18px}
.post .meta{font-size:10px;color:var(--muted)}
.post .meta b{color:var(--ink);font-weight:600}
.post h4{font-size:12px;color:var(--red);font-weight:600;margin:8px 0}
.post p{font-size:11px;color:var(--muted);line-height:1.6}
.post .more{font-size:11px;color:var(--red);font-weight:600;margin-top:12px;display:block}

/* partners */
.partners{height:108px;display:flex;justify-content:center;gap:22px}
.partners i{width:168px;height:100px;border:1px solid var(--line);display:flex;align-items:center;justify-content:center}
.partners i::after{content:"";width:70px;height:22px;background:#d4d4d4;border-radius:3px}

/* map */
.map{height:328px;margin-top:20px;position:relative;background:linear-gradient(135deg,#e4e4e4,#d6d6d6 60%,#e0e0e0)}
.map .pin{position:absolute;left:430px;top:150px}
.map .card{position:absolute;left:130px;top:100px;width:290px;height:150px;background:var(--white);padding:16px 20px;font-size:11px;line-height:1.6;box-shadow:0 4px 14px rgba(0,0,0,.12)}

/* footer */
.footer{height:372px;background:var(--footer);display:flex;padding:52px 140px 0}
.footer .about{width:420px}
.footer .brand{width:auto;font-size:22px}
.footer .social{display:flex;gap:10px;margin:24px 0 28px}
.footer .social i{width:24px;height:24px;border-radius:50%;background:var(--red);display:block}
.newsletter{display:flex}
.newsletter span{width:200px;height:34px;background:var(--white);border:1px solid var(--line);border-radius:17px 0 0 17px;font-size:11px;color:var(--muted);padding:8px 16px}
.newsletter b{height:34px;background:var(--red);color:var(--white);font-size:11px;font-weight:600;padding:9px 18px;border-radius:0 17px 17px 0}
.col{width:200px}
.col h4{color:var(--gold);font-size:15px;font-weight:700;margin-bottom:16px}
.col li{list-style:none;font-size:13px;color:#333;line-height:1.75}

.bottombar{height:56px;background:var(--black);color:#aaa;font-size:11px;display:flex;align-items:center;justify-content:space-between;padding:0 80px}
.cards{display:flex;gap:8px}
.cards i{width:30px;height:18px;background:#666;border-radius:2px;display:block}
</style>
</head>
<body>

<header>
  <div class="topbar">
    <div class="contact"><span>(012) 345 6789</span><span>hello@corvanthveylor.com</span></div>
    <div class="social"><i></i><i></i><i></i><i></i><i></i><i></i></div>
    <div class="prefs"><span>USD $</span><span>English</span><span>Setting</span></div>
  </div>
  <nav class="nav">
    <div class="brand"><span class="mark"></span>Corvanth Veylor</div>
    <div class="menu"><a>HOME</a><a>CATEGORY</a><a>SHOP</a><a>BLOG</a><a>CONTACT</a></div>
    <div class="tools">
      <svg width="14" height="14" viewBox="0 0 14 14"><circle cx="6" cy="6" r="4.5" fill="none" stroke="#222" stroke-width="1.6"/><line x1="9.5" y1="9.5" x2="13" y2="13" stroke="#222" stroke-width="1.6"/></svg>
      <svg width="16" height="14" viewBox="0 0 16 14"><path d="M1 1h3l2 8h8l1.5-6H5" fill="none" stroke="#222" stroke-width="1.5"/><circle cx="7" cy="12" r="1.3" fill="#222"/><circle cx="13" cy="12" r="1.3" fill="#222"/></svg>
      <svg width="14" height="14" viewBox="0 0 14 14"><circle cx="7" cy="4" r="3" fill="#222"/><path d="M1 14c0-4 3-6 6-6s6 2 6 6z" fill="#222"/></svg>
    </div>
  </nav>
</header>

<section class="hero">
  <div class="photo" role="img" aria-label="Portrait of a model with dark hair and bold red lips"></div>
  <div class="copy">
    <h1>Own Your Look, Bold And Unseen</h1>
    <p>Skincare and undetectable makeup for men who walk in with total confidence</p>
    <span class="btn">Shop Now</span>
  </div>
</section>

<section class="features">
  <div class="feature">
    <svg width="34" height="34" viewBox="0 0 34 34"><path d="M4 4h13l13 13-13 13L4 17z" fill="none" stroke="#ec1f27" stroke-width="2"/><circle cx="11" cy="11" r="2.5" fill="#ec1f27"/></svg>
    <h3>Discount system</h3>
    <p>Earn points with every order and trade them for savings on your next grooming routine, cleanser to liner.</p>
  </div>
  <div class="feature">
    <svg width="38" height="34" viewBox="0 0 38 34"><rect x="2" y="8" width="22" height="16" fill="none" stroke="#ec1f27" stroke-width="2"/><path d="M24 13h7l5 6v5H24z" fill="none" stroke="#ec1f27" stroke-width="2"/><circle cx="9" cy="27" r="3" fill="#ec1f27"/><circle cx="30" cy="27" r="3" fill="#ec1f27"/></svg>
    <h3>Free delivery</h3>
    <p>Orders over fifty dollars ship free, packed discreetly and sent to your door within three working days.</p>
  </div>
  <div class="feature">
    <svg width="40" height="34" viewBox="0 0 40 34"><circle cx="14" cy="11" r="6" fill="none" stroke="#ec1f27" stroke-width="2"/><circle cx="28" cy="13" r="4.5" fill="none" stroke="#ec1f27" stroke-width="2"/><path d="M3 31c0-7 5-11 11-11s11 4 11 11M25 22c6 0 11 3 11 9" fill="none" stroke="#ec1f27" stroke-width="2"/></svg>
    <h3>Support 24/7</h3>
    <p>Our skin experts answer shade and routine questions day and night by chat, mail or a quick phone call.</p>
  </div>
</section>

<section class="welcome">
  <div class="photo" role="img" aria-label="Cream jar with pink flowers and towels on a light surface"></div>
  <div class="card">
    <div class="eyebrow">ABOUT US</div>
    <h2>Welcome Corvanth Veylor</h2>
    <p>Skincare and undetectable makeup built for men, inspired by the myth of Corvanth. Clean formulas, honest guidance and looks that read natural. Every product ships with a tutorial so you learn to wear it with total confidence.</p>
    <span class="btn">Read More</span>
  </div>
</section>

<section class="trending">
  <h2 class="section-title">TOP TRENDING</h2>
  <p class="lead">Our most wanted essentials this season, chosen by men who care how they look. From a daily cleanser to a precise liner pen, each piece is made to work fast, feel light and stay invisible.</p>
  <div class="tabs"><span class="active">New products</span><span>Promo drop</span><span>Best sales</span></div>
  <div class="grid">
    <div class="product"><div class="img cleanser" role="img" aria-label="Face cleanser pump bottles"><span class="tag">new</span></div><h4>FACE CLEANSER</h4><div class="price">$ 29.00</div></div>
    <div class="product"><div class="img mask" role="img" aria-label="Mask in a round silver jar"></div><h4>MASK</h4><div class="price">$ 19.00</div></div>
    <div class="product"><div class="img moist" role="img" aria-label="Moisturizer pump container"><span class="tag">new</span></div><h4>MOISTURIZER</h4><div class="price">$ 34.00 <s>$ 40.00</s></div></div>
    <div class="product"><div class="img conceal" role="img" aria-label="Concealer click pen with brush and shade swatches"><span class="tag">new</span><div class="actions"><span>Quick View</span><span>Know Details</span></div></div><h4>CONCEALER</h4><div class="shades"><i style="background:#e8c3a0"></i><i style="background:#c48d62"></i><i style="background:#7a4c30"></i></div></div>
    <div class="product"><div class="img liner" role="img" aria-label="Black liquid liner pen"><span class="tag">new</span></div><h4>LIQUID LINER PEN</h4><div class="price">$ 22.00 <s>$ 28.00</s></div></div>

    <div class="product"><div class="img palette" role="img" aria-label="Contouring palette with brush"><span class="tag">new</span></div><h4>CONTOURING PALETTE</h4><div class="price">$ 38.00</div></div>
    <div class="product"><div class="img mask" role="img" aria-label="Mask in a round silver jar"></div><h4>MASK</h4><div class="price">$ 19.00</div></div>
    <div class="product"><div class="img moist" role="img" aria-label="Moisturizer pump container"><span class="tag">new</span></div><h4>MOISTURIZER</h4><div class="price">$ 34.00 <s>$ 40.00</s></div></div>
    <div class="product"><div class="img spray" role="img" aria-label="Row of setting spray bottles"><span class="tag">new</span></div><h4>SETTING SPRAY</h4><div class="price">$ 26.00 <s>$ 30.00</s></div></div>
    <div class="product"><div class="img liner" role="img" aria-label="Black liquid liner pen"><span class="tag">new</span></div><h4>LIQUID LINER PEN</h4><div class="price">$ 22.00 <s>$ 28.00</s></div></div>
  </div>
  <div class="all"><span class="btn">ALL PRODUCTS</span></div>
</section>

<section class="video">
  <div class="media" role="img" aria-label="Tutorial video still of a model touching her face">
    <div class="controls">
      <svg width="10" height="12" viewBox="0 0 10 12"><path d="M0 0l10 6-10 6z" fill="#fff"/></svg>
      <div class="bar"><b></b></div>
      <em>1:24</em>
      <svg width="14" height="12" viewBox="0 0 14 12"><path d="M0 4h3l4-4v12L3 8H0z" fill="#fff"/></svg>
    </div>
  </div>
  <div class="copy">
    <h2 class="section-title">OUR VIDEO</h2>
    <p>Short how-to films for every product in the line. Learn to prep, conceal and set in minutes, with shade tips and steps that keep your look sharp and natural.</p>
    <span class="btn">View more Tutorials</span>
  </div>
</section>

<section class="blog">
  <h2 class="section-title">BLOG POST</h2>
  <div class="posts">
    <article class="post">
      <div class="head"><div class="date"><b>02</b><small>AUG</small><i></i></div><div class="pic one" role="img" aria-label="Model with styled hair"></div></div>
      <div class="body"><div class="meta"><b>Corvanth</b> | By Corvanth</div><h4>Building a five minute routine</h4><p>Cleanse, treat and set before work. Our team shares the steps that keep skin clear and calm all day.</p><span class="more">Read More</span></div>
    </article>
    <article class="post">
      <div class="head"><div class="date"><b>02</b><small>AUG</small><i></i></div><div class="pic two" role="img" aria-label="Makeup artist working on a model"></div></div>
      <div class="body"><div class="meta"><b>Corvanth</b> | By Corvanth</div><h4>Finding your concealer shade</h4><p>Match in daylight, blend outward and check the jaw line. Three shades cover most skin tones.</p><span class="more">Read More</span></div>
    </article>
    <article class="post">
      <div class="head"><div class="date"><b>03</b><small>AUG</small><i></i></div><div class="pic three" role="img" aria-label="Model having makeup applied"></div></div>
      <div class="body"><div class="meta"><b>Corvanth</b> | By Corvanth</div><h4>Questions from our readers</h4><p>Your top questions on liner, contour and spray, answered by the people who make them.</p><span class="more">Read More</span></div>
    </article>
  </div>
</section>

<section class="partners" aria-label="Partners">
  <i></i><i></i><i></i><i></i><i></i>
</section>

<section class="map" role="img" aria-label="Street map showing the store location">
  <div class="card">
    <strong>Corvanth Veylor, 48 Marrow Lane, Halverton, CA 90210</strong><br>
    t : (012) 345 6789<br>
    hello@corvanthveylor.com<br>
    Mon - Sun : 09:00 - 18:00
  </div>
  <svg class="pin" width="24" height="32" viewBox="0 0 24 32"><path d="M12 0C5 0 0 5 0 12c0 9 12 20 12 20s12-11 12-20C24 5 19 0 12 0z" fill="#ec1f27"/><circle cx="12" cy="12" r="4.5" fill="#fff"/></svg>
</section>

<footer>
  <div class="footer">
    <div class="about">
      <div class="brand"><span class="mark"></span>Corvanth Veylor</div>
      <div class="social"><i></i><i></i><i></i><i></i><i></i></div>
      <div class="newsletter"><span>Enter your email</span><b>Subscribe</b></div>
    </div>
    <div class="col"><h4>Products</h4><ul><li>Prices drop</li><li>New products</li><li>Best sales</li></ul></div>
    <div class="col"><h4>Information</h4><ul><li>Legal Notice</li><li>Terms &amp; conditions</li><li>About us</li><li>Secure payment</li><li>Contact us</li></ul></div>
    <div class="col"><h4>Your account</h4><ul><li>Addresses</li><li>Credit slips</li><li>Orders</li><li>Personal info</li></ul></div>
  </div>
  <div class="bottombar">
    <span>Copyright © 2024 - All Rights Are Reserved</span>
    <div class="cards"><i></i><i></i><i></i><i></i></div>
    <span>Top</span>
  </div>
</footer>

</body>
</html>
```